Website development company website

ABOUT COMPANY
Hi everyone! We're a Melbourne, Australia website development company in a need of a website design that will make online store merchants want to engage our services.
We specialise exclusively in Torvista e-commerce platform (https://torvista-platform.example/). What distinguishes our business from competition is that rather than designing and building brand new websites, we offer development, support and maintenance services to established websites. Maintenance and Support are the keywords representing our business.
Our potential clients are people with broken, slow and underperforming Torvista installations who need assistance getting their websites up and making sales. Our website must pass the message that we can help, and provide quick means of making contact.
DESIGN
Overall, we're looking for a slick, clean, airy, conservative design. No need to do anything crazy, try to stick to what's "standard" in website design these days and make it easy on all of us. The website is unlikely to be updated too often so it needs to look attractive and fresh first time over and after a year, too.
Attached is our new logo, which you'll be able to take the basic idea from, the colors and fonts. Though, don't use the fonts from the logo in the website, stick to the standard widely supported fonts. Additional use of Google fonts is fine.
Don't overdo it with colors, stick to conservative basic color set and only use the colors from the log for accents like headings etc. Please, don't be tempted to use the blue and orange as background of whole blocks, other than perhaps footer. Thanks.
For the images used, I'd like to stay away from a design studio/digital agency feel and lean more towards professional support and maintenance services. I'm thinking images of content merchants doing their job. Something along the lines of "We'll be taking care of the website so that you only need to care about the business".
Some ideas I like:
http://www.plumframe-pics.example/detail/photo/portrait-of-confident-male-design-professional-royalty-free-image/572048163
http://www.plumframe-pics.example/detail/photo/designer-taking-picture-of-hat-high-res-stock-photography/839207514
http://www.plumframe-pics.example/detail/photo/woman-packaging-pottery-royalty-free-image/216684093
Images of colorful shopping bags and shopping carts are over the top and not serious enough. Instead of images matching Online Shopping, I'd try going more for Stability, Reliability, Performance.
Our existing website is http://www.bravuln.example. Please, don't take design ideas from it, but it will give you a picture of the structure of our new website and content that's going to be used initially.
If you could include a basic icon set to use throughout the website, that would be great. If the icons could match our logo (attached), it would be a big plus.
ALL PAGES
Every page must contain clearly visible phone number (1300 648 907) and a Contact Us Now button, which opens an AJAX driven popup form with Name, Email, Phone and Message to be sent through.
To start with, main menu items will be Torvista, Portfolio, Contact.
At the bottom of each page, please, include a newsletter subscription form with text Subscribe to Torvista Support and Security Updates.
For the footer, I'd like to see a logo strip with the following logos in grayscale (no need to link anywhere): Torvista, QRX, DataVane, NCB. You'll find the logos on Google Images.
Standard footer columns follow. Here, I'd like to see logos in color: Torvista Certified Developer, Torvista Ceritified Solution Provider. Again, the logos are on Google Images.
No social media logos/links necessary anywhere on the website.
...and then the copyright line.
FRONT PAGE
Large slider with images that would appeal to our target audience. Keywords here would be Torvista System Audit, Torvista Performance Optimisation, Torvista Website Emergency Recovery, Torvista Development Infrastructure Hosting. We'll have a static page created for each of these to link to.
In a corner of the slider, or on the edge, can I have an overlay with logos in color (same as footer): Torvista Certified Developer, Torvista Ceritified Solution Provider.
Underneath, a number of blocks, each with an image and teaser that we'll use to link to various pages throughout the website.
PORTFOLIO PAGE
I'm thinking a single long page with a block per client, which will contain project name, description from us and a testimonial from client. Also, each block will contain a single large screenshot. No gallery or slideshow is necessary here, just one image per project.
I'll leave the layout up to you, but try to put yourself in the shoes of a potential client reviewing our past work by simply scrolling down this one page.
CONTACT US PAGE
Separate page with the same form as above, phone number (1300 648 907), email address (support@kavreo.example), address (Suite 42, Level 3|8 Wattlebrook Lane|Fernvale Heights VIC 3999), and a grayscale Geomapa.
CODING UP
Coding up into static HTML/CSS/JS is equally important as the design itself. We're a website development company, we'll be integrating the theme. We will spot any issues and we will point them out.
Coded up design must be fully responsive. Enough said.
To be able to create any content in future, we'd like one extra page coded up with samples of all themed elements, lists, forms, buttons, 2, 3, 4-column layout, alerts, icons, etc. This page does not need to be designed, only coded up.
The design will be integrated into Drupal using Twig. If possible at all, try to keep it in mind when designing and coding up, and make the integration into a Drupal theme easier for us.
GOOD LUCK!
That's it. Let me know if anything needs clarifying. So far I've had a great experience with ArtFlockly. I don't doubt some great designs will emerge. Clever ideas are highly appreciated, but also make it clear you've read and followed the points in this brief. Cheers, Tom

```html
<!DOCTYPE html>
<html lang="en">
<head>
<meta charset="utf-8">
<title>Kavreo E-commerce — Torvista Development, Support and Maintenance</title>
<link rel="stylesheet" href="https://fonts.googleapis.com/css2?family=Open+Sans:wght@300;400;600;700&family=Montserrat:wght@700&display=swap">
<style>
:root{
  --navy:#1b4b80;
  --navy-dark:#143a66;
  --orange:#e8821e;
  --ink:#333;
  --muted:#777;
  --light:#9a9a9a;
  --strip:#e9eaec;
  --portfolio-bg:#d8e0e8;
  --footer:#262626;
  --footer-base:#1c1c1c;
  --white:#fff;
}
*{box-sizing:border-box;margin:0;padding:0}
html,body{width:1200px;height:2970px;overflow:hidden}
body{font-family:"Open Sans",Arial,sans-serif;color:var(--ink);background:var(--white);position:relative}
.section{position:relative;width:1200px}
.abs{position:absolute}
.center{text-align:center}

/* header */
.site-header{height:88px;border-top:4px solid var(--navy);box-shadow:0 1px 4px rgba(0,0,0,.08);z-index:2}
.top-accent{position:absolute;top:-4px;left:0;width:160px;height:4px;background:var(--orange)}
.brand{left:130px;top:18px;display:flex;align-items:center;gap:10px}
.brand-mark{width:34px;height:40px;background:var(--orange)}
.brand-name{font-weight:700;font-size:30px;color:var(--navy);letter-spacing:-.5px}
.main-nav{left:414px;top:30px;display:flex;gap:30px;font-size:13px;color:#444}
.main-nav a{color:inherit;text-decoration:none;position:relative}
.main-nav a.active{color:var(--navy);font-weight:600}
.main-nav a.active::after{content:"";position:absolute;left:0;right:0;bottom:-28px;height:3px;background:var(--navy)}
.nav-sep{width:1px;height:56px;background:#ddd;left:900px;top:14px}
.call{right:130px;top:22px;text-align:right}
.call small{display:block;font-size:13px;color:#555}
.call strong{display:block;font-size:23px;color:var(--orange);font-weight:700;line-height:1.2}

/* hero */
.hero{height:490px;background:radial-gradient(ellipse at 50% 40%,#8d9398 0%,#5d6368 55%,#3c4145 100%);overflow:hidden}
.hero-photo{position:absolute;inset:0}
.hero-title{top:158px;left:0;right:0;font-family:"Montserrat",Arial,sans-serif;font-size:30px;line-height:52px;color:var(--white);letter-spacing:2px;text-transform:uppercase}
.hero-actions{top:282px;left:0;right:0;display:flex;justify-content:center;gap:18px}
.btn{display:inline-block;font-size:14px;padding:0 24px;height:36px;line-height:34px;text-decoration:none;border:2px solid transparent}
.btn-orange{background:var(--orange);color:var(--white);width:126px;text-align:center}
.btn-outline{border-color:var(--white);color:var(--white);width:128px;text-align:center}
.slide-arrow{top:218px;width:52px;height:52px;background:rgba(40,40,40,.75);display:flex;align-items:center;justify-content:center}

/* tech strip */
.tech-strip{height:100px;display:flex;align-items:center}
.tech-strip.grey{background:var(--strip)}
.tech-item{position:absolute;transform:translateX(-50%);font-size:30px;font-weight:700;color:#a9a9a9;letter-spacing:.5px}

/* welcome */
.welcome{height:480px}
.welcome-kicker{top:44px;left:0;right:0;font-size:13px;color:#444}
.welcome-lead{top:70px;left:0;right:0;font-size:24px;font-weight:300;line-height:35px;color:#444}
.welcome-lead b{font-weight:600;color:var(--navy-dark)}
.feature{width:430px;transform:translateX(-50%);text-align:center;top:180px}
.feature h3{font-size:17px;font-weight:600;margin:22px 0 18px;color:#222}
.feature p{font-size:11.5px;line-height:21px;color:#666}
.welcome-divider{left:600px;top:178px;width:1px;height:214px;background:#ddd}

/* services */
.services{height:510px;background:linear-gradient(135deg,var(--navy) 0%,#1e568f 45%,var(--navy-dark) 100%);color:var(--white)}
.section-title{font-size:24px;font-weight:300}
.section-title b{font-weight:600}
.services .section-title{top:40px;left:0;right:0}
.services .sub{top:88px;left:0;right:0;font-size:13px;color:#b7c9dd}
.service-card{top:175px;width:294px;height:148px;background:var(--white);color:var(--ink);text-align:center;padding-top:66px;box-shadow:0 2px 6px rgba(0,0,0,.2)}
.service-icon{position:absolute;left:50%;top:-36px;transform:translateX(-50%);width:80px;height:80px;border-radius:50%;display:flex;align-items:center;justify-content:center}
.service-card h4{font-size:17px;font-weight:600;color:#222}
.service-card p{font-size:11.5px;line-height:21px;color:#777;margin-top:4px;padding:0 12px}
.btn-ghost{display:inline-block;margin-top:10px;font-size:11px;color:#aaa;background:#eee;padding:3px 18px}
.services .tagline{top:412px;left:0;right:0;font-size:13px;color:#b7c9dd}
.services .cta{top:444px;left:519px;width:162px;height:36px;border:2px solid var(--white);font-size:14px;line-height:32px;text-align:center;color:var(--white)}

/* testimonials */
.testimonials{height:313px}
.testimonials .section-title{top:34px;left:0;right:0;color:#333}
.testimonials .sub{top:80px;left:0;right:0;font-size:13px;color:#444}
.client-photo{left:133px;top:155px;width:110px;height:110px;border-radius:50%;background:linear-gradient(160deg,#c9d3dc,#5b6d82)}
.quote-rule{left:287px;top:152px;width:1px;height:120px;background:#ddd}
.quote{left:313px;top:152px;width:760px;font-size:13px;line-height:26px;color:#555}
.quote-author{left:313px;top:241px;font-size:14px;font-weight:700;color:var(--orange)}
.quote-author span{font-weight:400;color:#999}

/* portfolio */
.portfolio{height:505px;background:var(--portfolio-bg)}
.portfolio .section-title{top:34px;left:0;right:0;color:#333}
.portfolio .sub{top:72px;left:0;right:0;font-size:13px;color:#444}
.project{top:135px;width:212px;height:242px;background:var(--white);box-shadow:0 1px 3px rgba(0,0,0,.15)}
.project-shot{height:198px}
.project-name{height:44px;line-height:44px;text-align:center;font-size:13px;color:#444}
.port-arrow{top:228px}
.view-more{top:440px;left:519px;width:162px;height:37px;border:2px solid var(--orange);color:var(--orange);font-size:14px;line-height:33px;text-align:center}

/* footer */
.site-footer{height:325px;background:var(--footer);color:#ccc}
.footer-col h5{font-size:16px;font-weight:600;color:var(--orange);margin-bottom:22px}
.footer-col ul{list-style:none;font-size:11.5px;line-height:28px}
.footer-col p{font-size:11.5px;line-height:22px}
.news-input{margin-top:16px;width:232px;height:35px;background:#3a3a3a;display:flex;align-items:center;padding-left:12px;gap:8px;font-size:11px;color:#888}
.news-submit{margin-top:10px;width:109px;height:36px;background:var(--orange);color:var(--white);font-weight:700;font-size:14px;line-height:36px;text-align:center}
.map{left:794px;top:50px;width:276px;height:156px;background:linear-gradient(135deg,#e6e9e2,#cfdcc7 60%,#d8d9d5)}
.map-link{left:797px;top:214px;font-size:11.5px;color:#ccc;text-decoration:underline}
.copyright{height:59px;background:var(--footer-base);color:#ccc;font-size:12px;line-height:59px;text-align:center}
.copyright span{color:var(--orange)}
</style>
</head>
<body>

<header class="section site-header">
  <div class="top-accent"></div>
  <div class="abs brand"><div class="brand-mark"></div><span class="brand-name">Kavreo</span></div>
  <nav class="abs main-nav">
    <a class="active" href="#">Home</a><a href="#">About Us</a><a href="#">Torvista</a><a href="#">Our Portfolio</a><a href="#">Contact Us</a>
  </nav>
  <div class="abs nav-sep"></div>
  <div class="abs call"><small>Call Us Now!</small><strong>1300 648 907</strong></div>
</header>

<section class="section hero">
  <div class="hero-photo" role="img" aria-label="Dimmed photo of a desk with a keyboard and mouse"></div>
  <h1 class="abs hero-title center">High performance Torvista sites<br>on time and on budget.</h1>
  <div class="abs hero-actions"><a class="btn btn-orange" href="#">Read More</a><a class="btn btn-outline" href="#">Contact Us</a></div>
  <div class="abs slide-arrow" style="left:0"><svg width="14" height="22" viewBox="0 0 14 22"><path d="M11 3 3 11l8 8" fill="none" stroke="#fff" stroke-width="3"/></svg></div>
  <div class="abs slide-arrow" style="right:0"><svg width="14" height="22" viewBox="0 0 14 22"><path d="M3 3l8 8-8 8" fill="none" stroke="#fff" stroke-width="3"/></svg></div>
</section>

<section class="section tech-strip grey">
  <span class="tech-item" style="left:154px;top:34px">Hexmark</span>
  <span class="tech-item" style="left:333px;top:34px">Torvista</span>
  <span class="tech-item" style="left:509px;top:34px">Corvane</span>
  <span class="tech-item" style="left:695px;top:34px">QRX</span>
  <span class="tech-item" style="left:838px;top:34px">NCB</span>
  <span class="tech-item" style="left:1006px;top:34px">DataVane</span>
</section>

<section class="section welcome">
  <p class="abs welcome-kicker center">Welcome to Kavreo E-commerce</p>
  <p class="abs welcome-lead center">New generation websites by <b>new generation designers.</b><br>For new generation entrepreneurs..</p>
  <div class="abs feature" style="left:349px">
    <svg width="64" height="52" viewBox="0 0 64 52"><rect x="4" y="3" width="56" height="38" fill="none" stroke="#e8821e" stroke-width="3"/><path d="M2 48h60" stroke="#e8821e" stroke-width="3"/><path d="M24 15l-7 7 7 7M40 15l7 7-7 7M35 13l-6 18" fill="none" stroke="#e8821e" stroke-width="2.5"/></svg>
    <h3>Torvista Certified Developer</h3>
    <p>It is a long established fact that a reader will be distracted by the readable content of a page when looking at its layout. The point of using Lorem Ipsum is that it has a more-or-less normal distribution of letters, as opposed to using , making it look like readable English.</p>
  </div>
  <div class="welcome-divider abs"></div>
  <div class="abs feature" style="left:879px;top:170px">
    <svg width="64" height="62" viewBox="0 0 64 62"><path d="M32 12a15 15 0 0 0-9 27v7h18v-7a15 15 0 0 0-9-27z" fill="none" stroke="#e8821e" stroke-width="3"/><path d="M25 52h14M27 57h10M32 2v5M12 10l4 4M52 10l-4 4M6 27h5M53 27h5" stroke="#e8821e" stroke-width="3"/></svg>
    <h3>Torvista Certified Solution Provider</h3>
    <p>It is a long established fact that a reader will be distracted by the readable content of a page when looking at its layout. The point of using Lorem Ipsum is that it has a more-or-less normal distribution of letters, as opposed to using , making it look like readable English.</p>
  </div>
</section>

<section class="section services">
  <h2 class="abs section-title center">What <b>We Do</b></h2>
  <p class="abs sub center">Simply dummy text of the printing and typesetting industry.</p>
  <div class="abs service-card" style="left:133px">
    <div class="service-icon" style="background:#5bb5b0"><svg width="40" height="36" viewBox="0 0 40 36"><rect x="2" y="2" width="36" height="24" rx="2" fill="#fff"/><rect x="6" y="6" width="28" height="16" fill="#e0584a"/><path d="M16 30h8v-4h-8zM12 33h16" stroke="#fff" stroke-width="3"/><path d="M17 10l-3 4 3 4M23 10l3 4-3 4" fill="none" stroke="#fff" stroke-width="1.6"/></svg></div>
    <h4>Web Development</h4>
    <p>It is a long established fact that a reader will be distracted the readable content.</p>
    <span class="btn-ghost">Read More</span>
  </div>
  <div class="abs service-card" style="left:453px">
    <div class="service-icon" style="background:#f3efe8" role="img" aria-label="Illustration of a support agent with headset"></div>
    <h4>Web Support</h4>
    <p>It is a long established fact that a reader will be distracted the readable content.</p>
    <span class="btn-ghost">Read More</span>
  </div>
  <div class="abs service-card" style="left:774px">
    <div class="service-icon" style="background:#5bb5b0"><svg width="40" height="40" viewBox="0 0 40 40"><path d="M8 32 26 14" stroke="#fff" stroke-width="6" stroke-linecap="round"/><circle cx="29" cy="11" r="7" fill="#fff"/><path d="M32 32 14 14" stroke="#f4b640" stroke-width="6" stroke-linecap="round"/><circle cx="11" cy="11" r="5" fill="#f4b640"/></svg></div>
    <h4>Web Maintenance</h4>
    <p>It is a long established fact that a reader will be distracted the readable content.</p>
    <span class="btn-ghost">Read More</span>
  </div>
  <p class="abs tagline center">High performance Torvista sites on time and on budget.</p>
  <a class="abs cta" href="#">Contact Us Now!</a>
</section>

<section class="section testimonials">
  <h2 class="abs section-title center">Client <b>Testimonials</b></h2>
  <p class="abs sub center">What our Customers say About us and Reviews</p>
  <div class="abs client-photo" role="img" aria-label="Portrait photo of a client"></div>
  <div class="abs quote-rule"></div>
  <p class="abs quote">" Lorem Ipsum is simply dummy text of the printing and typesetting industry. Lorem Ipsum has been the industry's standard dummy text ever since the 1500s, when an unknown printer took a galley of type and scrambled it to make a type specimen book. It has survived not only five centuries "</p>
  <p class="abs quote-author">Neil Arkwright, <span>USA</span></p>
</section>

<section class="section portfolio">
  <h2 class="abs section-title center">Our <b>Portfolio</b></h2>
  <p class="abs sub center">Simply dummy text of the printing and typesetting industry.</p>
  <svg class="abs port-arrow" style="left:58px" width="22" height="64" viewBox="0 0 22 64"><path d="M20 2 2 32l18 30" fill="none" stroke="#555" stroke-width="1.5"/></svg>
  <div class="abs project" style="left:131px"><div class="project-shot" role="img" aria-label="Screenshot of a medical clinic website" style="background:linear-gradient(180deg,#2f6fae,#cfdde9)"></div><div class="project-name">Our project name 01</div></div>
  <div class="abs project" style="left:374px"><div class="project-shot" role="img" aria-label="Screenshot of a creative design website" style="background:linear-gradient(180deg,#f0f0f0,#d23a3a)"></div><div class="project-name">Our project name 02</div></div>
  <div class="abs project" style="left:616px"><div class="project-shot" role="img" aria-label="Screenshot of a wedding website" style="background:linear-gradient(180deg,#58a9d8,#f3f6f8)"></div><div class="project-name">Our project name 03</div></div>
  <div class="abs project" style="left:857px"><div class="project-shot" role="img" aria-label="Screenshot of a travel website" style="background:linear-gradient(180deg,#4a8e4c,#e6eef4)"></div><div class="project-name">Our project name 04</div></div>
  <svg class="abs port-arrow" style="left:1122px" width="22" height="64" viewBox="0 0 22 64"><path d="M2 2l18 30L2 62" fill="none" stroke="#555" stroke-width="1.5"/></svg>
  <a class="abs view-more" href="#">View More</a>
</section>

<section class="section tech-strip">
  <span class="tech-item" style="left:154px;top:34px">Hexmark</span>
  <span class="tech-item" style="left:333px;top:34px">Torvista</span>
  <span class="tech-item" style="left:509px;top:34px">Corvane</span>
  <span class="tech-item" style="left:695px;top:34px">QRX</span>
  <span class="tech-item" style="left:838px;top:34px">NCB</span>
  <span class="tech-item" style="left:1006px;top:34px">DataVane</span>
</section>

<footer class="section site-footer">
  <div class="abs footer-col" style="left:131px;top:46px">
    <h5>Quick Links</h5>
    <ul><li>- Home</li><li>- About Us</li><li>- Torvista</li><li>- Our Portfolio</li><li>- Contact Us</li></ul>
  </div>
  <div class="abs footer-col" style="left:287px;top:46px;width:240px">
    <h5>Sign Up Newsletter</h5>
    <p>Simply dummy text of the printing and typesetting industry.</p>
    <div class="news-input"><svg width="12" height="9" viewBox="0 0 12 9"><rect width="12" height="9" fill="#ccc"/><path d="M0 0l6 5 6-5" fill="none" stroke="#3a3a3a"/></svg>Email Address</div>
    <div class="news-submit">Submit</div>
  </div>
  <div class="abs footer-col" style="left:562px;top:46px;width:220px">
    <h5>Contact Us</h5>
    <p>Suite 42, Level 3, 8 Wattlebrook Lane,<br>Fernvale Heights VIC 3999</p>
    <p style="margin-top:6px">Phone:<br>1300 648 907</p>
    <p style="margin-top:6px">Email:<br>info@kavreo.example</p>
  </div>
  <div class="abs map" role="img" aria-label="Street map showing the office location"></div>
  <a class="abs map-link" href="#">View Geomapa</a>
</footer>
<div class="section copyright">Copyright © 2016 - <span>Kavreo E-commerce</span>. All Rights Reserved</div>

</body>
</html>
```